BRTL web site redesign

Coastal Linkage Engineering service (BRTL) is a diverse technology company specialising in design and installation of fibre optics, network convergence and building services, for commercial clients in Australia, we required a new design of our website to attract new clients, generate sales leads, and provide information about our services to the market. The site and should have a new technology look and feel and be designed in word press. our branding colour is blue.

Target Market(s)

New developments, Construction organisations, Commercial end users, IT managers, Consultants.

Industry/Entity Type

It Company

Number of Pages Required

5+ page

Font styles to use
Sans Serif

Colors
0292cd
3176b5

Requirements
Must have
• key pages.
• Home page with some sizzle, automated pictures running through, I like the look of this competitor website http://www.gleamwirex.com.au/ good clean menus and easy to navigate.
• Services page our key services are Fibre optics, Security, Building services,Electrical. I would like the same page layout (Design) for all our services, with a find out more link on each page, manly picture driven with text around our key messaging.
• About us page with space for company profile and directors pictures, bio and contact information.
• Certifications / Accreditations page with have over 20 certifications on different products from suppliers, and a number of licences from governing bodies.
• Current and past projects page with case studies and customer outcomes
• Contact us page with options around what services they require more information on, please keep in mind the site is around generating sales Leeds and being seen as an industry expert.
Nice to have
• RSS feeds, Linked in link, to be placed within the design, Consistent BRTL branding,Same colour blue as our logo Document library for education information, white papers, presentations etc,
• a new technology look and feel, mobile friendly.
Should not have
• boring layout, move away from our cuurent website http://www.brtlgroup.com.au/
• no e eCommerce store required.

```html
<!DOCTYPE html>
<html lang="en">
<head>
<meta charset="utf-8">
<title>BRTL – Coastal Linkage Engineering Service</title>
<link rel="stylesheet" href="https://fonts.googleapis.com/css2?family=Open+Sans:wght@400;600;700&display=swap">
<style>
  :root {
    --brand-blue: #0292cd;
    --brand-deep: #3176b5;
    --link-blue: #1a8fc9;
    --ink: #333333;
    --ink-soft: #555555;
    --white: #ffffff;
    --night: #050708;
    --footer: #111111;
    --caption: rgba(30, 30, 30, 0.72);
  }
  * { box-sizing: border-box; margin: 0; padding: 0; }
  html, body { width: 710px; height: 1200px; overflow: hidden; background: var(--white); }
  body { font-family: "Open Sans", Arial, sans-serif; color: var(--ink); position: relative; }
  .abs { position: absolute; }

  /* Header */
  .site-header { position: absolute; left: 0; top: 0; width: 710px; height: 78px; background: var(--brand-blue); box-shadow: 0 2px 3px rgba(0,0,0,.35); z-index: 3; }
  .brand { position: absolute; left: 31px; top: 6px; width: 130px; height: 66px; background: var(--white); display: flex; align-items: center; justify-content: center; gap: 6px; }
  .brand-mark { width: 10px; height: 10px; background: var(--brand-blue); }
  .brand-name { font-size: 28px; font-weight: 700; color: var(--brand-blue); letter-spacing: 1px; }
  .main-nav a { position: absolute; top: 31px; font-size: 7.6px; font-weight: 600; color: var(--white); text-decoration: none; text-transform: uppercase; white-space: nowrap; }
  .dropdown { position: absolute; left: 318px; top: 45px; width: 107px; background: var(--white); z-index: 4; box-shadow: 0 1px 3px rgba(0,0,0,.25); }
  .dropdown a { display: block; height: 20px; line-height: 20px; padding-left: 4px; font-size: 7.2px; color: var(--brand-blue); text-decoration: none; border-bottom: 1px solid #9fd3ea; }
  .dropdown::before { content: ""; position: absolute; left: 8px; top: -4px; border: 4px solid transparent; border-top: 0; border-bottom-color: var(--white); }

  /* Hero */
  .hero { position: absolute; left: 0; top: 78px; width: 710px; height: 272px; background: linear-gradient(90deg, #b7b8b4 0%, #6e7377 25%, #d9dadc 55%, #e9eaec 75%, #8a8b8d 100%); }
  .hero-caption { position: absolute; left: 0; top: 224px; width: 710px; height: 48px; background: var(--caption); }
  .hero-caption h1 { position: absolute; left: 31px; top: 17px; font-size: 10.4px; font-weight: 700; color: var(--white); text-transform: uppercase; white-space: nowrap; }
  .slider-dots { position: absolute; left: 638px; top: 27px; display: flex; gap: 2px; }
  .slider-dots span { width: 5px; height: 5px; border: 1px solid var(--white); }
  .slider-dots span:first-child { background: var(--white); }

  /* About */
  .section-title { position: absolute; font-size: 14px; font-weight: 400; color: #222; text-shadow: 0 1px 1px rgba(0,0,0,.2); }
  .intro { position: absolute; left: 31px; top: 410px; width: 640px; font-size: 6.6px; line-height: 13px; color: var(--ink); }

  .service-card { position: absolute; top: 468px; width: 144px; }
  .service-photo { width: 144px; height: 92px; border: 1px solid #222; box-shadow: 1px 1px 2px rgba(0,0,0,.35); }
  .service-card h2 { margin-top: 10px; font-size: 11px; font-weight: 400; color: var(--link-blue); }
  .service-card p { margin-top: 3px; font-size: 6.6px; line-height: 13px; color: var(--ink); }
  .btn-small { display: inline-block; margin-top: 7px; width: 53px; height: 20px; line-height: 20px; text-align: center; font-size: 6.6px; color: var(--white); background: var(--brand-blue); text-decoration: none; box-shadow: 0 2px 2px rgba(0,0,0,.35); }

  /* Banner */
  .security-banner { position: absolute; left: 0; top: 697px; width: 710px; height: 190px; background: radial-gradient(ellipse at 12% 30%, #1d4a5e 0%, #0b1c24 35%, var(--night) 65%); }
  .security-banner h2 { position: absolute; left: 0; width: 710px; text-align: center; top: 44px; font-size: 18px; font-weight: 400; color: var(--white); }
  .banner-rule { position: absolute; left: 141px; top: 75px; width: 429px; height: 1px; background: #5a6266; }
  .security-banner p { position: absolute; left: 180px; width: 350px; top: 83px; text-align: center; font-size: 7px; line-height: 13px; color: var(--white); }
  .btn-outline { position: absolute; left: 314px; top: 124px; width: 82px; height: 22px; line-height: 20px; border: 1px solid var(--white); border-radius: 2px; text-align: center; font-size: 9.6px; color: var(--white); text-decoration: none; letter-spacing: .5px; }

  /* Projects */
  .project { position: absolute; width: 170px; }
  .project h3 { font-size: 7.4px; font-weight: 400; color: var(--link-blue); white-space: nowrap; }
  .project time { display: block; margin-top: 4px; font-size: 6.6px; color: #222; }
  .project p { margin-top: 3px; font-size: 6.4px; line-height: 13.3px; color: var(--ink-soft); }

  /* Footer */
  .site-footer { position: absolute; left: 0; top: 1162px; width: 710px; height: 38px; background: var(--footer); color: var(--white); font-size: 6.6px; text-align: center; line-height: 38px; }
  .site-footer span { margin: 0 5px; }
</style>
</head>
<body>

<header class="site-header">
  <div class="brand"><span class="brand-mark"></span><span class="brand-name">BRTL</span></div>
  <nav class="main-nav">
    <a href="#" style="left:274px">Home</a>
    <a href="#" style="left:318px">Services</a>
    <a href="#" style="left:375px">About Us</a>
    <a href="#" style="left:434px">Certifications</a>
    <a href="#" style="left:513px">Current / Past Projects</a>
    <a href="#" style="left:634px">Contact Us</a>
  </nav>
  <div class="dropdown">
    <a href="#">FIBRE OPTICS</a>
    <a href="#">SECURITY</a>
    <a href="#">BUILDING SERVICES</a>
    <a href="#" style="border-bottom:0">ELECTRICAL</a>
  </div>
</header>

<section class="hero" role="img" aria-label="Technician in a suit working on a laptop beside a server rack">
  <div class="hero-caption">
    <h1>BRTL is diversified technology company 100% Australian owned and operated</h1>
    <div class="slider-dots"><span></span><span></span><span></span><span></span><span></span></div>
  </div>
</section>

<h2 class="section-title" style="left:32px;top:372px">About BRTL Group</h2>
<p class="intro">BRTL is diversified technology company 100% Australian owned and operated, we provide Communication, Electrical, Security &amp; ICT services for residential and commercial customers. With over 100 years of combined industry knowledge we pride ourselves on innovated solutions that utilises technology advancements which delivers on our customer's expectations.</p>

<article class="service-card" style="left:31px">
  <div class="service-photo" role="img" aria-label="Fibre splicing equipment and cables" style="background:linear-gradient(135deg,#6b5a48,#2a2f35 55%,#8a6a4a)"></div>
  <h2>Fibre Optics</h2>
  <p>Proin gravida nibh vel velit auctored aliquetenean sollicitudin lorem quis bibendum auctornisi elit.</p>
  <a class="btn-small" href="#">READ MORE</a>
</article>
<article class="service-card" style="left:200px">
  <div class="service-photo" role="img" aria-label="Security surveillance cameras" style="background:linear-gradient(135deg,#1e1c2a,#8e8e9a 50%,#2b2838)"></div>
  <h2>Security</h2>
  <p>Proin gravida nibh vel velit auctored aliquetenean sollicitudin lorem quis bibendum auctornisi elit.</p>
  <a class="btn-small" href="#">READ MORE</a>
</article>
<article class="service-card" style="left:369px">
  <div class="service-photo" role="img" aria-label="Person using a building control touch screen" style="background:linear-gradient(135deg,#0c4f8a,#2aa4e0 55%,#0a3f74)"></div>
  <h2>Building Services</h2>
  <p>Proin gravida nibh vel velit auctored aliquetenean sollicitudin lorem quis bibendum auctornisi elit.</p>
  <a class="btn-small" href="#">READ MORE</a>
</article>
<article class="service-card" style="left:535px">
  <div class="service-photo" role="img" aria-label="Electrical conduits and wiring in a switch room" style="background:linear-gradient(135deg,#c9c4bb,#6f6a63 50%,#b8b2a8)"></div>
  <h2>Electrical</h2>
  <p>Proin gravida nibh vel velit auctored aliquetenean sollicitudin lorem quis bibendum auctornisi elit.</p>
  <a class="btn-small" href="#">READ MORE</a>
</article>

<section class="security-banner" role="img" aria-label="Glowing fibre optic strands on a dark background">
  <h2>BRTL offers a wide range of IP commercial security solutions</h2>
  <div class="banner-rule"></div>
  <p>Proin gravida nibh vel velit auctor aliquet. Aenean sollicitudin, lorem quis bibendum auctor, nisi elit consequat ipsum, nec sagittis sem nibh id elit.</p>
  <a class="btn-outline" href="#">READ MORE</a>
</section>

<h2 class="section-title" style="left:31px;top:910px">Current / Past Projects</h2>

<article class="project" style="left:52px;top:954px">
  <h3>Proin gravida nibh vel velit auctor aliquet</h3><time>12 Jan 2015</time>
  <p>Lorem Ipsum. Proin gravida nibh vel velit ws uctor aliquet lorem quis bibendum auctor nisi elit consequat ipsum nec sagitti.</p>
</article>
<article class="project" style="left:269px;top:954px">
  <h3>Gravida nibh vel velit auctor aliquet vild</h3><time>12 Jan 2015</time>
  <p>Lorem Ipsum. Proin gravida nibh vel velit ws uctor aliquet lorem quis bibendum auctor nisi elit consequat ipsum nec sagitti.</p>
</article>
<article class="project" style="left:494px;top:954px">
  <h3>Hroin gravida nibh vel velit auctor aliquet</h3><time>12 Jan 2015</time>
  <p>Lorem Ipsum. Proin gravida nibh vel velit ws uctor aliquet lorem quis bibendum auctor nisi elit consequat ipsum nec sagitti.</p>
</article>
<article class="project" style="left:52px;top:1053px">
  <h3>Aroin gravida nibh vel velit auctor aliquet</h3><time>10 Jan 2015</time>
  <p>Lorem Ipsum. Proin gravida nibh vel velit ws uctor aliquet lorem quis bibendum auctor nisi elit consequat ipsum nec sagitti.</p>
</article>
<article class="project" style="left:269px;top:1053px">
  <h3>Proin gravida nibh vel velit auctor aliquet</h3><time>10 Jan 2015</time>
  <p>Lorem Ipsum. Proin gravida nibh vel velit ws uctor aliquet lorem quis bibendum auctor nisi elit consequat ipsum nec sagitti.</p>
</article>
<article class="project" style="left:494px;top:1053px">
  <h3>Aravida nibh vel velit auctor aliquet seed</h3><time>10 Jan 2015</time>
  <p>Lorem Ipsum. Proin gravida nibh vel velit ws uctor aliquet lorem quis bibendum auctor nisi elit consequat ipsum nec sagitti.</p>
</article>

<footer class="site-footer">
  <span>©Copyright 2014 brtlgroup</span>|<span>All rights reserved</span>|<span>Privacy policy</span>|<span>Terms &amp; Conditions</span>
</footer>

</body>
</html>
```